Volbrey Inc Business Card

Looking to get an updated business card for a Contract Machining company (www.volbreyinc.example) - looking for a clean design the portrays the technical nature of the business - colors can follow the website design and be in any combination that makes sense (red black, white, metallic or silver) - logos attached for use also. Would like space for: Name, title, business phone (555 214-3086), cell phone , website (www.volbreyinc.example) - possibly QR code could be integrated for website (designer choice), business address - 418 Harlow Bend, Brennick Falls, MI 48199 (cards will be for 4 employees, I will either need to modify a template or I can provide individual information)
Target Market(s)
Aerospace, defense and medical device manufacturing companies that need machining
Industry/Entity Type
Machining for aerospace, defense, medical
Contact Information for Business Card
Name, Title, Business Phone, Cell Phone, email, business website and business address
Look and feel

```html
<!DOCTYPE html>
<html lang="en">
<head>
<meta charset="utf-8">
<title>Volbrey Inc Business Card</title>
<link href="https://fonts.googleapis.com/css2?family=Montserrat:wght@400;700&display=swap" rel="stylesheet">
<style>
  :root {
    --bg: #d3d3d3;
    --paper: #f1f0ee;
    --red: #b31b21;
    --ink: #6f6f6f;
    --rule: #dcdbd8;
  }
  html, body {
    margin: 0;
    width: 1200px;
    height: 1051px;
    overflow: hidden;
    background: var(--bg);
    font-family: "Montserrat", sans-serif;
  }
  .canvas {
    position: relative;
    width: 1200px;
    height: 1051px;
  }
  .card {
    position: absolute;
    left: 280px;
    width: 640px;
    height: 366px;
    background: var(--paper);
    border-bottom: 4px solid var(--red);
    box-shadow: 0 18px 40px rgba(0,0,0,0.18);
    box-sizing: border-box;
  }
  .card--front { top: 110px; }
  .card--back { top: 575px; }

  .brand {
    position: absolute;
    left: 0;
    top: 0;
    width: 270px;
    height: 100%;
    display: flex;
    flex-direction: column;
    align-items: center;
    justify-content: center;
    gap: 18px;
  }
  .brand__dot {
    width: 120px;
    height: 120px;
    border-radius: 50%;
    background: var(--red);
  }
  .brand__name {
    color: var(--red);
    font-weight: 700;
    font-size: 26px;
    letter-spacing: 1px;
    white-space: nowrap;
  }
  .divider {
    position: absolute;
    left: 270px;
    top: 60px;
    width: 2px;
    height: 246px;
    background: var(--rule);
    box-shadow: 1px 0 0 #fff;
  }
  .details {
    position: absolute;
    left: 310px;
    top: 62px;
    right: 30px;
    color: var(--ink);
  }
  .details__name {
    margin: 0;
    color: var(--red);
    font-weight: 700;
    font-size: 22px;
    letter-spacing: 0.5px;
  }
  .details__title {
    margin: 2px 0 24px;
    font-size: 15px;
  }
  .details__address {
    margin: 0 0 24px;
    font-size: 15px;
    line-height: 1.45;
    font-style: normal;
  }
  .contact {
    list-style: none;
    margin: 0;
    padding: 0;
    font-size: 15px;
    line-height: 1.6;
  }
  .contact li {
    display: flex;
    align-items: center;
    gap: 9px;
    white-space: nowrap;
  }
  .contact svg {
    width: 13px;
    height: 13px;
    fill: var(--red);
    flex: none;
  }
  .back-mark {
    position: absolute;
    left: 50%;
    top: 50%;
    width: 130px;
    height: 130px;
    margin: -65px 0 0 -65px;
    border-radius: 50%;
    background: var(--red);
  }
</style>
</head>
<body>
<div class="canvas">
  <section class="card card--front">
    <div class="brand">
      <div class="brand__dot"></div>
      <div class="brand__name">VOLBREY INC</div>
    </div>
    <div class="divider"></div>
    <div class="details">
      <h1 class="details__name">MARCUS DENVALE</h1>
      <p class="details__title">President</p>
      <address class="details__address">418 Harlow Bend<br>Brennick Falls, MI 48199</address>
      <ul class="contact">
        <li><svg viewBox="0 0 24 24"><path d="M6.6 10.8a15 15 0 0 0 6.6 6.6l2.2-2.2c.3-.3.7-.4 1-.2 1.1.4 2.3.6 3.6.6.6 0 1 .4 1 1V20c0 .6-.4 1-1 1A17 17 0 0 1 3 4c0-.6.4-1 1-1h3.5c.6 0 1 .4 1 1 0 1.3.2 2.5.6 3.6.1.3 0 .7-.2 1z"/></svg>555 214-3086</li>
        <li><svg viewBox="0 0 24 24"><path d="M2 5h20v14H2zm2 2v.5l8 5 8-5V7z"/></svg>m.denvale@volbreyinc.example</li>
        <li><svg viewBox="0 0 24 24"><path d="M12 2a10 10 0 1 0 0 20 10 10 0 0 0 0-20zm6.9 6h-3a15 15 0 0 0-1.3-3.6A8 8 0 0 1 18.9 8zM12 4c.8 1.2 1.5 2.5 1.9 4h-3.8c.4-1.5 1.1-2.8 1.900-4zM4.3 14a8 8 0 0 1 0-4h3.4a16 16 0 0 0 0 4zm.8 2h3a15 15 0 0 0 1.3 3.6A8 8 0 0 1 5.1 16zm3-8h-3a8 8 0 0 1 4.3-3.6A15 15 0 0 0 8.1 8zM12 20c-.8-1.2-1.5-2.5-1.9-4h3.8c-.4 1.5-1.1 2.8-1.9 4zm2.3-6H9.7a14 14 0 0 1 0-4h4.6a14 14 0 0 1 0 4zm.3 5.6A15 15 0 0 0 15.9 16h3a8 8 0 0 1-4.3 3.6zm1.7-5.6a16 16 0 0 0 0-4h3.4a8 8 0 0 1 0 4z"/></svg>www.volbreyinc.example</li>
      </ul>
    </div>
  </section>

  <section class="card card--back">
    <div class="back-mark"></div>
  </section>
</div>
</body>
</html>
```